A business card design for a dental office. We have Two doctors working here. We practice general de

I already have a logo designed for the office with the name and a slogan.
Now I need to create design for a business card using the same logo.
Details Needed on the front side of the card are :
Bernard K. Oswin, DDS
Gerald M Fenwick, DDS
418 Birch Lane
Alderby, NV 00000
Phone : 555 019 4831
Fax : 555 019 4832
Website : WWW.BrightmoorToothHaven.Com
Office hours by appointment
On the back side of the card need :
Appointment
Date....................Time...................
With....................................
If unable to keep your appointment, please give 24-48 hours notice in order to avoid broken appointment fee.

Industry/Entity Type

Dental Clinic

Contact Information for Business Card

Bernard K. Oswin, DDS
Gerald M Fenwick, DDS
418 Birch Lane
Alderby, NV 00000
Phone : 555 019 4831
Fax : 555 019 4832
Appointment

Requirements
Must have
• Keep the Name and slogan on the logo on the front of the card. You can move them around the Logo and Name/Slogan of business (Oswin Family Dentistry/We bring out your best smile) as you wish to get a feel of the design.
• Bernard K. Oswin, DDS
• Gerald M Fenwick, DDS
• 418 Birch Lane
• Alderby, NV 00000
• Phone : 555 019 4831
• Fax : 555 019 4832
• WWW.BrightmoorToothHaven.Com
• Keep these three groups above as they are together now in different areas of the front side.
• On the back side of the card need :
• Appointment
• Date....................Time...................
• With....................................
• If unable to keep your appointment, please give 24-48 hours notice in order to avoid broken appointment fee.

```html
<!DOCTYPE html>
<html lang="en">
<head>
<meta charset="UTF-8">
<title>Oswin Family Dentistry – Business Card</title>
<link rel="stylesheet" href="https://fonts.googleapis.com/css2?family=Cinzel:wght@400;700&family=Arimo:wght@400&display=swap">
<style>
  :root {
    --brand-blue: #1c68a8;
    --title-blue: #1f5fa6;
    --slogan-red: #d9353f;
    --ink: #2b2b2b;
    --ink-soft: #555;
    --card-white: #f7f7f6;
    --backdrop: #e7e4df;
    --logo-teal: #2fb3a0;
  }
  * { margin: 0; padding: 0; box-sizing: border-box; }
  html, body { width: 1200px; height: 892px; overflow: hidden; }
  body {
    background: var(--backdrop);
    display: flex;
    align-items: center;
    justify-content: center;
    gap: 40px;
    font-family: "Arimo", Arial, sans-serif;
    color: var(--ink);
  }
  .card {
    position: relative;
    width: 540px;
    height: 309px;
    background: var(--card-white);
    border: 10px solid var(--brand-blue);
    box-shadow: 0 4px 14px rgba(0,0,0,.18);
  }

  /* ---------- front ---------- */
  .brand { position: absolute; left: 26px; top: 22px; display: flex; align-items: center; gap: 16px; }
  .brand-mark {
    width: 78px; height: 78px; border-radius: 50%;
    background: var(--logo-teal);
  }
  .brand-name {
    font-family: "Cinzel", serif; font-weight: 700; font-size: 25px;
    color: var(--title-blue); letter-spacing: .5px; line-height: 1;
  }
  .slogan {
    display: flex; align-items: center; gap: 8px; margin-top: 9px;
    font-family: "Arimo", Arial, sans-serif; font-size: 9px; letter-spacing: 2.2px;
    text-transform: uppercase; color: var(--slogan-red);
  }
  .slogan::before, .slogan::after { content: ""; width: 22px; height: 1px; background: var(--slogan-red); }

  .doctors { position: absolute; left: 28px; top: 136px; }
  .doctor { margin-bottom: 14px; font-family: "Cinzel", serif; color: var(--ink-soft); line-height: 1.15; }
  .doctor-name { font-size: 15px; letter-spacing: 1px; }
  .doctor-title { font-size: 13px; letter-spacing: 1px; }

  .divider { position: absolute; left: 228px; top: 134px; width: 1px; height: 132px; background: #9aa3ab; }

  .contact { position: absolute; left: 244px; top: 138px; list-style: none; }
  .contact li { display: flex; align-items: flex-start; gap: 8px; font-size: 13px; line-height: 16px; margin-bottom: 9px; color: var(--ink); }
  .contact svg { flex: none; width: 16px; height: 16px; }

  /* ---------- back ---------- */
  .appointment-title {
    position: absolute; left: 0; right: 0; top: 28px; text-align: center;
    font-family: "Cinzel", serif; font-weight: 700; font-size: 30px;
    color: var(--title-blue); letter-spacing: 2px;
  }
  .days { position: absolute; left: 40px; right: 40px; top: 86px; display: flex; justify-content: space-between; }
  .day { display: flex; flex-direction: column; align-items: center; gap: 8px; font-size: 15px; letter-spacing: .5px; }
  .day-box { width: 30px; height: 28px; border: 1.5px solid #444; }

  .fields { position: absolute; left: 30px; right: 30px; top: 170px; }
  .field-row { display: flex; align-items: flex-end; gap: 8px; margin-bottom: 18px; font-size: 16px; }
  .field-line { flex: 1; border-bottom: 2px solid #222; height: 1px; margin-bottom: 4px; }
  .field-row.with { justify-content: center; padding-left: 80px; }
  .field-row.with .field-line { flex: none; width: 180px; }
</style>
</head>
<body>

<section class="card card-front" aria-label="Front of business card">
  <div class="brand">
    <div class="brand-mark" aria-hidden="true"></div>
    <div>
      <div class="brand-name">Oswin Family Dentistry</div>
      <div class="slogan">We bring out your best smile</div>
    </div>
  </div>

  <div class="doctors">
    <div class="doctor"><div class="doctor-name">Bernard K. Oswin</div><div class="doctor-title">DDS</div></div>
    <div class="doctor"><div class="doctor-name">Gerald M Fenwick</div><div class="doctor-title">DDS</div></div>
  </div>

  <div class="divider"></div>

  <ul class="contact">
    <li>
      <svg viewBox="0 0 16 16" aria-label="Phone"><rect width="16" height="16" rx="2" fill="#1c68a8"/><path d="M5 3.5l2 2-1 1.2c.6 1.3 1.6 2.3 2.8 2.8l1.2-1 2 2-1.2 1.5C7.5 11.8 4.2 8.5 3.5 5z" fill="#fff"/></svg>
      <span>555 019 4831</span>
    </li>
    <li>
      <svg viewBox="0 0 16 16" aria-label="Fax"><rect width="16" height="16" rx="2" fill="#1c68a8"/><rect x="4.5" y="3" width="7" height="4" fill="#fff"/><rect x="3" y="7" width="10" height="5" rx="1" fill="#fff"/><rect x="5" y="9" width="6" height="1" fill="#1c68a8"/></svg>
      <span>555 019 4832</span>
    </li>
    <li>
      <svg viewBox="0 0 16 16" aria-label="Website"><rect width="16" height="16" rx="2" fill="#1c68a8"/><circle cx="8" cy="8" r="4.6" fill="none" stroke="#fff" stroke-width="1.2"/><ellipse cx="8" cy="8" rx="2" ry="4.6" fill="none" stroke="#fff" stroke-width="1"/><line x1="3.4" y1="8" x2="12.6" y2="8" stroke="#fff" stroke-width="1"/></svg>
      <span>WWW.BrightmoorToothHaven.Com</span>
    </li>
    <li>
      <svg viewBox="0 0 16 16" aria-label="Address"><rect width="16" height="16" rx="2" fill="#1c68a8"/><path d="M8 13s-3.5-3.8-3.5-6.3a3.5 3.5 0 0 1 7 0C11.5 9.2 8 13 8 13z" fill="#fff"/><circle cx="8" cy="6.7" r="1.3" fill="#1c68a8"/></svg>
      <span>418 Birch Lane<br>Alderby, NV 00000</span>
    </li>
  </ul>
</section>

<section class="card card-back" aria-label="Back of business card">
  <h1 class="appointment-title">Appointment</h1>

  <div class="days">
    <div class="day">MON<span class="day-box"></span></div>
    <div class="day">TUE<span class="day-box"></span></div>
    <div class="day">WED<span class="day-box"></span></div>
    <div class="day">THU<span class="day-box"></span></div>
    <div class="day">FRI<span class="day-box"></span></div>
  </div>

  <div class="fields">
    <div class="field-row"><span>Date :-</span><span class="field-line"></span><span>Time :-</span><span class="field-line"></span></div>
    <div class="field-row"><span>Date :-</span><span class="field-line"></span><span>Time :-</span><span class="field-line"></span></div>
    <div class="field-row with"><span>With :-</span><span class="field-line"></span></div>
  </div>
</section>

</body>
</html>
```